Brell Stone Company Business Cards

Front and Back Business Card - logo and text setup - cool design. I need workable photoshop or illustrator files so I can setup each employee card with design that is created
Updates

Hi everyone, thank you for the great entries. Please no more white and blue cards - there are so many already - black and silver only now please. thanks!

Target Market(s)

Construction Industry - Facility Managers

Industry/Entity Type

Construction

Contact Information for Business Card

I really like contemporary simplistic looks - clean neat....not opposed to seeing some black backrounds

Requirements
Must have
• Logo/website address with design on front only - www.brellstone-example.com (logo attached)
• Back:
• Name/Title/Company Address/Phone/email address
Nice to have
• Cool design
Should not have
• Nothing gimmicky like Fire or Water - since we are a Fire Protection company - it has all been done

```html
<!DOCTYPE html>
<html lang="en">
<head>
<meta charset="utf-8">
<title>Brell Stone Company Business Cards</title>
<link rel="stylesheet" href="https://fonts.googleapis.com/css2?family=Poppins:wght@400;600;800&family=Roboto+Condensed:wght@400&display=swap">
<style>
  :root {
    --black: #141414;
    --black-band: #1b1b1c;
    --black-emboss: #262627;
    --silver: #bfc3c9;
    --silver-light: #e3e5e8;
    --card-light: #f4f4f5;
    --grey-text: #4a4d52;
    --backdrop: #e9e8e6;
  }
  * { box-sizing: border-box; margin: 0; padding: 0; }
  html, body {
    width: 1200px; height: 920px; overflow: hidden;
    background: var(--backdrop);
    font-family: "Poppins", sans-serif;
  }
  .sheet {
    position: relative; width: 1200px; height: 920px;
    display: flex; align-items: center; justify-content: center; gap: 40px;
  }
  .card {
    position: relative; width: 540px; height: 310px; overflow: hidden;
    box-shadow: 0 6px 18px rgba(0,0,0,0.2);
  }
  /* Front */
  .card-front { background: var(--black); }
  .front-wordmark {
    position: absolute; left: 0; right: 0; top: 112px; text-align: center;
    font-weight: 800; font-size: 52px; letter-spacing: -1px;
    color: var(--black-emboss);
  }
  .front-web {
    position: absolute; left: 0; right: 0; bottom: 26px; text-align: center;
    font-size: 14px; letter-spacing: 1px; color: var(--silver);
  }
  .front-web .accent { color: var(--silver-light); }
  /* Back */
  .card-back { background: var(--card-light); }
  .back-wordmark {
    position: absolute; left: 0; right: 0; top: 38px; text-align: center;
    font-weight: 800; font-size: 46px; letter-spacing: -1px;
    color: var(--black);
  }
  .info-band {
    position: absolute; left: 0; right: 0; top: 140px; height: 88px;
    background: var(--black-band);
    display: flex; align-items: center;
  }
  .identity {
    width: 282px; text-align: right; padding-right: 14px;
    border-right: 1px solid var(--silver);
    height: 58px; display: flex; flex-direction: column; justify-content: center;
  }
  .person-name {
    font-family: "Roboto Condensed", sans-serif; font-size: 27px;
    color: var(--silver); text-transform: uppercase; line-height: 1.1;
  }
  .person-title { font-size: 12px; color: var(--silver-light); margin-top: 6px; }
  .contact-list { list-style: none; padding-left: 12px; }
  .contact-list li {
    display: flex; align-items: center; gap: 9px;
    font-size: 13px; color: var(--silver-light); line-height: 19px;
  }
  .contact-list svg { width: 11px; height: 11px; flex: none; }
  .address-line {
    position: absolute; left: 0; right: 0; top: 262px; text-align: center;
    font-size: 12.5px; color: var(--grey-text);
  }
  .address-line .company { font-weight: 600; color: var(--black); margin-right: 4px; }
</style>
</head>
<body>
<main class="sheet">
  <section class="card card-front" aria-label="Card front">
    <div class="front-wordmark">brellstone inc.</div>
    <p class="front-web">www.<span class="accent">brellstone-example</span>.com</p>
  </section>

  <section class="card card-back" aria-label="Card back">
    <div class="back-wordmark">brellstone inc.</div>
    <div class="info-band">
      <div class="identity">
        <span class="person-name">Dana Whitfield</span>
        <span class="person-title">Director</span>
      </div>
      <ul class="contact-list">
        <li>
          <svg viewBox="0 0 12 12" aria-hidden="true"><path d="M2.5 1 L4.5 1 L5.2 3.5 L4 4.5 C4.7 6 6 7.3 7.5 8 L8.5 6.8 L11 7.5 L11 9.5 C11 10.3 10.3 11 9.5 11 C5 11 1 7 1 2.5 C1 1.7 1.7 1 2.5 1 Z" fill="var(--silver)"/></svg>
          (555) 014-2290
        </li>
        <li>
          <svg viewBox="0 0 12 12" aria-hidden="true"><rect x="1" y="2.5" width="10" height="7" fill="none" stroke="var(--silver)" stroke-width="1.2"/><path d="M1 2.5 L6 6.5 L11 2.5" fill="none" stroke="var(--silver)" stroke-width="1.2"/></svg>
          info@brellstone-example.com
        </li>
        <li>
          <svg viewBox="0 0 12 12" aria-hidden="true"><circle cx="6" cy="6" r="5" fill="none" stroke="var(--silver)" stroke-width="1.1"/><ellipse cx="6" cy="6" rx="2.2" ry="5" fill="none" stroke="var(--silver)" stroke-width="1"/><path d="M1 6 H11" stroke="var(--silver)" stroke-width="1"/></svg>
          www.brellstone-example.com
        </li>
      </ul>
    </div>
    <p class="address-line"><span class="company">brellstone inc.</span>48 Meridian Way Eastfield, NY 10000</p>
  </section>
</main>
</body>
</html>
```